Innovative Event Ticketing Start Up. Needs a Web Design

We need a web design for a new company based in London called 'Bandwise'. We are a platform which facilitates the building of groups of customers for events. As more people commit to an event, the price incrementally decreases. We would like there to be an emphasis on the sharing element and the decreasing price with higher participation.

Any quieres please email me at rvkm47@postlane.net

Target Market(s)

18-30 year olds who are active and savvy across social media sites

Industry/Entity Type

Events

Number of Pages Required

3 page

Font styles to use
Other font styles liked:
• Phi Roman

Requirements
Must have
• Each event offering runs for a limited time so a countdown timer is also to be included as well as a counter of number of participants (please find example attached).
• The interface needs to have the options for 'Live 'Music', 'Nightlife', 'Festivals', 'Comedy' and 'Everything Else'. Also
• A 'featured' section, for our promoted events
• Social sharing icons for Chatterbox, Flitter, PingTalk, SMS and Email
• Room the inclusion of a video
• Pages for clients to sign up - registering details ect.
• Content is still being completed, so room available to add when ready
Nice to have
• An interface design we like as a guiding templates on is https://quorvaapp.com/
• Luma wordpress theme is also of interest.
• Scroll over clicking for main interface and also for the event once clicked upon.
• Event pages similar desgin to quorva with same features such as Google Maps but also participant counter and affiliate marketing options.
Should not have
• CMS no longer necessary

```html
<!DOCTYPE html>
<html lang="en">
<head>
<meta charset="utf-8">
<title>Bandwise — Events</title>
<link rel="stylesheet" href="https://fonts.googleapis.com/css2?family=Raleway:wght@400;600;700;800&family=Open+Sans:ital,wght@0,400;0,600;1,400;1,600&display=swap">
<style>
:root{
  --orange:#f05a28;
  --orange-dark:#d9481a;
  --ink:#2a2a2a;
  --grey:#777;
  --light:#f2f2f2;
  --line:#e3e3e3;
  --footer:#333333;
  --white:#ffffff;
}
*{box-sizing:border-box;margin:0;padding:0}
html,body{width:1200px;height:3556px;overflow:hidden}
body{position:relative;background:var(--white);font-family:"Open Sans",Arial,sans-serif;color:var(--ink)}
.abs{position:absolute}
h2,h3,h4,.nav a,.btn,.brand-name{font-family:"Raleway",Arial,sans-serif}

/* header */
.site-header{left:0;top:0;width:1200px;height:108px;background:var(--orange)}
.brand{left:100px;top:18px;display:flex;align-items:center;gap:14px}
.brand-mark{width:72px;height:72px;background:var(--white);border-radius:8px}
.brand-name{color:var(--white);font-weight:700;font-size:24px}
.nav{right:60px;top:42px;display:flex;gap:48px}
.nav a{color:var(--white);text-decoration:none;font-size:16px;font-weight:600}

/* hero */
.hero{left:0;top:108px;width:1200px;height:532px;background:radial-gradient(ellipse at 38% 45%,#4aa6e8 0%,#1c4d8f 22%,#0d1a3a 55%,#05070f 100%)}
.hero-arrow{top:340px}
.hero-copy{left:650px;top:450px;width:500px;color:var(--white)}
.hero-copy h1{font-family:"Raleway",Arial,sans-serif;font-weight:800;font-size:38px;letter-spacing:1px;margin-bottom:8px}
.hero-copy p{font-style:italic;font-weight:600;font-size:18px;line-height:1.4}

/* section titles */
.section-title{left:0;width:1200px;text-align:center;font-weight:800;font-size:30px;letter-spacing:1px}
.section-sub{left:0;width:1200px;text-align:center;font-size:13px}
.t-orange{color:var(--orange)}
.t-white{color:var(--white)}

/* welcome */
.welcome-text{left:180px;top:738px;width:840px;text-align:center;font-size:13px;line-height:1.7;color:var(--grey)}
.feature{width:230px;text-align:center;top:812px}
.feature-icon{width:70px;height:70px;border:2px solid var(--orange);margin:0 auto 16px;display:flex;align-items:center;justify-content:center}
.feature h4{font-size:16px;font-weight:700;margin-bottom:8px}
.feature p{font-size:12px;color:var(--grey);line-height:1.6}

/* dark photo bands */
.band-photo{left:0;width:1200px}
.upcoming-bg{top:1030px;height:610px;background:linear-gradient(180deg,#1b3158 0%,#26406b 35%,#101522 100%)}
.featured-bg{top:2010px;height:630px;background:linear-gradient(180deg,#6a3a2e 0%,#3a2a28 40%,#151313 100%)}

/* event cards */
.card{width:236px;background:var(--white);overflow:hidden}
.card-photo{width:236px;height:196px}
.card-body{padding:18px 16px 0;text-align:center}
.card-body h4{color:var(--orange);font-size:18px;font-weight:700;margin-bottom:8px}
.card-body p{font-size:12px;color:var(--grey);line-height:1.6;height:58px}
.share-row{border-top:1px solid var(--line);margin-top:14px;height:34px;display:flex;align-items:center;justify-content:center;gap:9px;font-size:10px;color:var(--orange);font-weight:600}
.btn{display:flex;align-items:center;justify-content:center;gap:8px;background:var(--orange);color:var(--white);font-weight:700;font-size:13px;width:130px;height:38px;left:535px;border-radius:2px}

/* featured cards */
.fcard{width:236px;background:var(--white);overflow:hidden}
.fcard-photo{width:236px;height:200px}
.fcard-lower{display:flex;height:170px}
.fcard-strip{width:42px;background:var(--orange);display:flex;flex-direction:column;align-items:center;justify-content:space-around;padding:10px 0}
.fcard-body{flex:1;padding:16px 14px}
.fcard-body h4{color:var(--orange);font-size:18px;font-weight:700;margin-bottom:8px}
.fcard-body p{font-size:12px;color:var(--grey);line-height:1.6}

/* counters */
.counter{width:200px;text-align:center;top:1760px}
.counter-ring{position:relative;width:140px;height:140px;margin:0 auto}
.counter-ring .num{position:absolute;left:0;top:36px;width:140px;font-family:"Raleway",Arial,sans-serif;font-weight:800;font-size:36px;color:var(--ink)}
.counter-ring .cap{position:absolute;left:0;top:84px;width:140px;font-size:11px;color:var(--grey)}
.counter h4{margin-top:22px;color:var(--orange);font-size:16px;font-weight:800;letter-spacing:1px}

/* videos */
.video-main{left:100px;top:2760px;width:620px;height:290px;border:6px solid var(--light);background:linear-gradient(135deg,#1e5e6e 0%,#3a8a8f 40%,#0f2a33 100%)}
.play{left:372px;top:2868px}
.video-item{left:780px;width:320px;display:flex;gap:20px}
.video-thumb{width:96px;height:84px;border:3px solid var(--light)}
.video-item h4{color:var(--orange);font-size:15px;font-weight:700;margin:4px 0 6px}
.video-item p{font-size:12px;color:var(--grey);line-height:1.5}
.thumb-a{background:linear-gradient(135deg,#2d5a3d,#7aa86a)}
.thumb-b{background:linear-gradient(135deg,#3a3a4a,#9a8a80)}
.thumb-c{background:linear-gradient(135deg,#555,#ccc)}

/* footer */
.site-footer{left:0;top:3180px;width:1200px;height:376px;background:var(--footer);color:#ccc}
.footer-h{font-family:"Raleway",Arial,sans-serif;color:var(--white);font-weight:700;font-size:16px;letter-spacing:.5px}
.map{left:100px;top:3230px;width:230px;height:120px;background:linear-gradient(135deg,#dfe6d8,#c8d3e0)}
.copyright{left:100px;top:3380px;font-size:11px;color:#aaa}
.contact-line{left:480px;display:flex;gap:14px;font-size:12px;line-height:1.6;width:300px}
.footer-social{left:480px;top:3390px;display:flex;gap:14px;font-size:11px;color:var(--white);font-weight:600}
.register{left:860px;top:3190px;width:240px;height:350px;background:var(--orange);padding:22px 22px}
.register h4{font-family:"Raleway",Arial,sans-serif;color:var(--white);font-size:16px;font-weight:800;margin-bottom:20px;letter-spacing:1px}
.field{display:block;height:34px;background:var(--white);margin-bottom:14px;font-size:12px;color:#999;padding:8px 10px}
.submit{width:110px;height:34px;margin:18px auto 0;background:var(--white);color:var(--orange);font-family:"Raleway",Arial,sans-serif;font-weight:800;font-size:13px;display:flex;align-items:center;justify-content:center}
</style>
</head>
<body>

<header class="site-header abs">
  <div class="brand abs"><span class="brand-mark"></span><span class="brand-name">Bandwise</span></div>
  <nav class="nav abs">
    <a href="#">Home</a><a href="#">Pages</a><a href="#">Features</a><a href="#">events</a><a href="#">Calendar</a><a href="#">Contacts</a><a href="#">Reservations</a>
  </nav>
</header>

<section class="hero abs" role="img" aria-label="Photo of a curved wall of glowing event screens in blue and amber light"></section>
<svg class="hero-arrow abs" style="left:28px" width="20" height="36" viewBox="0 0 20 36"><path d="M17 2 3 18l14 16" stroke="#fff" stroke-width="3" fill="none"/></svg>
<svg class="hero-arrow abs" style="right:28px" width="20" height="36" viewBox="0 0 20 36"><path d="M3 2l14 16L3 34" stroke="#fff" stroke-width="3" fill="none"/></svg>
<div class="hero-copy abs">
  <h1>BANDWISE</h1>
  <p>Lorem Ipsum is simply dummy text of the printing and type-setting industry. Lorem Ipsum has been the industry's standard dummy text</p>
</div>

<!-- welcome -->
<h2 class="section-title t-orange abs" style="top:676px">WELCOME TO BANDWISE</h2>
<p class="welcome-text abs">Lorem ipsum is simply dummy text of the printing and typesetting industry. Lorem ipsum has been the industry's standard dummy text ever since the 1500s, when an unknown printer took a galley of type and scrambled it to make a type specimen book. It has survived not only five centuries but also the leap.</p>

<div class="feature abs" style="left:120px">
  <div class="feature-icon"><svg width="34" height="30" viewBox="0 0 34 30"><path d="M17 28 4 15a7.5 7.5 0 0 1 13-10 7.5 7.5 0 0 1 13 10z" fill="var(--orange)"/></svg></div>
  <h4>7/24 everytime events</h4><p>Lorem ipsum is simply dummy text of the printing and typesetting industry.</p>
</div>
<div class="feature abs" style="left:360px">
  <div class="feature-icon"><svg width="32" height="32" viewBox="0 0 32 32"><rect x="3" y="6" width="26" height="23" fill="none" stroke="var(--orange)" stroke-width="2.5"/><path d="M3 13h26M10 2v7M22 2v7" stroke="var(--orange)" stroke-width="2.5"/></svg></div>
  <h4>25+ Events Location</h4><p>Lorem ipsum is simply dummy text of the printing and typesetting industry.</p>
</div>
<div class="feature abs" style="left:610px">
  <div class="feature-icon"><svg width="34" height="32" viewBox="0 0 34 32"><path d="M2 15a15 13 0 0 1 30 0z" fill="var(--orange)"/><path d="M17 15v12a3 3 0 0 1-6 0" stroke="var(--orange)" stroke-width="2.5" fill="none"/></svg></div>
  <h4>30+ Speakers</h4><p>Lorem ipsum is simply dummy text of the printing and typesetting industry.</p>
</div>
<div class="feature abs" style="left:850px">
  <div class="feature-icon"><svg width="32" height="32" viewBox="0 0 32 32"><path d="M16 2l4.2 9 9.8 1-7.4 6.6 2.2 9.6L16 23.2 7.2 28.2l2.2-9.6L2 12l9.8-1z" fill="var(--orange)"/></svg></div>
  <h4>Party After Events</h4><p>Lorem ipsum is simply dummy text of the printing and typesetting industry.</p>
</div>

<!-- upcoming events -->
<div class="band-photo upcoming-bg abs" role="img" aria-label="Dark photo of a concert crowd with raised hands under stage lights"></div>
<h2 class="section-title t-white abs" style="top:1064px">UPCOMING EVENTS</h2>
<p class="section-sub t-white abs" style="top:1106px">Lorem ipsum is simply dummy text of the printing and typesetting industry.</p>

<article class="card abs" style="left:100px;top:1150px">
  <div class="card-photo" style="background:linear-gradient(135deg,#5a4a2a,#c9a55a)" role="img" aria-label="Photo of saxophones on a stage"></div>
  <div class="card-body"><h4>Live Music</h4><p>Lorem ipsum is simply dummy text of the printing and typesetting industry.</p></div>
  <div class="share-row"><svg width="14" height="10" viewBox="0 0 14 10"><rect x=".7" y=".7" width="12.6" height="8.6" fill="none" stroke="var(--orange)" stroke-width="1.4"/><path d="M1 1l6 5 6-5" stroke="var(--orange)" stroke-width="1.4" fill="none"/></svg><span>Chatterbox</span><span>Flitter</span><span>PingTalk</span><span>SMS</span></div>
</article>
<article class="card abs" style="left:354px;top:1150px">
  <div class="card-photo" style="background:linear-gradient(135deg,#3a2a6a,#d05aa0)" role="img" aria-label="Photo of a nightclub dance floor in purple light"></div>
  <div class="card-body"><h4>Nightlife</h4><p>Lorem ipsum is simply dummy text of the printing and typesetting industry.</p></div>
  <div class="share-row"><svg width="14" height="10" viewBox="0 0 14 10"><rect x=".7" y=".7" width="12.6" height="8.6" fill="none" stroke="var(--orange)" stroke-width="1.4"/><path d="M1 1l6 5 6-5" stroke="var(--orange)" stroke-width="1.4" fill="none"/></svg><span>Chatterbox</span><span>Flitter</span><span>PingTalk</span><span>SMS</span></div>
</article>
<article class="card abs" style="left:608px;top:1150px">
  <div class="card-photo" style="background:linear-gradient(135deg,#c08a4a,#f0d8a0)" role="img" aria-label="Photo of a festival crowd in warm sunlight"></div>
  <div class="card-body"><h4>Festivals</h4><p>Lorem ipsum is simply dummy text of the printing and typesetting industry.</p></div>
  <div class="share-row"><svg width="14" height="10" viewBox="0 0 14 10"><rect x=".7" y=".7" width="12.6" height="8.6" fill="none" stroke="var(--orange)" stroke-width="1.4"/><path d="M1 1l6 5 6-5" stroke="var(--orange)" stroke-width="1.4" fill="none"/></svg><span>Chatterbox</span><span>Flitter</span><span>PingTalk</span><span>SMS</span></div>
</article>
<article class="card abs" style="left:862px;top:1150px">
  <div class="card-photo" style="background:linear-gradient(135deg,#8a6a7a,#e0c8d0)" role="img" aria-label="Photo of comedy performers in costume"></div>
  <div class="card-body"><h4>Comedy</h4><p>Lorem ipsum is simply dummy text of the printing and typesetting industry.</p></div>
  <div class="share-row"><svg width="14" height="10" viewBox="0 0 14 10"><rect x=".7" y=".7" width="12.6" height="8.6" fill="none" stroke="var(--orange)" stroke-width="1.4"/><path d="M1 1l6 5 6-5" stroke="var(--orange)" stroke-width="1.4" fill="none"/></svg><span>Chatterbox</span><span>Flitter</span><span>PingTalk</span><span>SMS</span></div>
</article>
<a class="btn abs" style="top:1552px"><svg width="16" height="12" viewBox="0 0 16 12"><rect x="1" y="1" width="14" height="10" rx="2" fill="none" stroke="#fff" stroke-width="1.6"/><circle cx="8" cy="6" r="2" fill="#fff"/></svg>READ MORE</a>

<!-- band together -->
<h2 class="section-title t-orange abs" style="top:1680px">BAND TOGETHER</h2>

<div class="counter abs" style="left:150px">
  <div class="counter-ring"><svg width="140" height="140" viewBox="0 0 140 140"><circle cx="70" cy="70" r="62" fill="none" stroke="var(--line)" stroke-width="10"/><circle cx="70" cy="70" r="62" fill="none" stroke="var(--orange)" stroke-width="10" stroke-dasharray="290 400" transform="rotate(-90 70 70)"/></svg><span class="num">680</span><span class="cap">lorem ipsum</span></div>
  <h4>LOREM IPSUM</h4>
</div>
<div class="counter abs" style="left:390px">
  <div class="counter-ring"><svg width="140" height="140" viewBox="0 0 140 140"><circle cx="70" cy="70" r="62" fill="none" stroke="var(--line)" stroke-width="10"/><circle cx="70" cy="70" r="62" fill="none" stroke="var(--orange)" stroke-width="10" stroke-dasharray="290 400" transform="rotate(-90 70 70)"/></svg><span class="num">680</span><span class="cap">lorem ipsum</span></div>
  <h4>LOREM IPSUM</h4>
</div>
<div class="counter abs" style="left:630px">
  <div class="counter-ring"><svg width="140" height="140" viewBox="0 0 140 140"><circle cx="70" cy="70" r="62" fill="none" stroke="var(--line)" stroke-width="10"/><circle cx="70" cy="70" r="62" fill="none" stroke="var(--orange)" stroke-width="10" stroke-dasharray="290 400" transform="rotate(-90 70 70)"/></svg><span class="num">680</span><span class="cap">lorem ipsum</span></div>
  <h4>LOREM IPSUM</h4>
</div>
<div class="counter abs" style="left:870px">
  <div class="counter-ring"><svg width="140" height="140" viewBox="0 0 140 140"><circle cx="70" cy="70" r="62" fill="none" stroke="var(--line)" stroke-width="10"/><circle cx="70" cy="70" r="62" fill="none" stroke="var(--orange)" stroke-width="10" stroke-dasharray="290 400" transform="rotate(-90 70 70)"/></svg><span class="num">680</span><span class="cap">lorem ipsum</span></div>
  <h4>LOREM IPSUM</h4>
</div>

<!-- feature events -->
<div class="band-photo featured-bg abs" role="img" aria-label="Dark photo of a festival crowd with hands in the air"></div>
<h2 class="section-title t-white abs" style="top:2046px">FEATURE EVENTS</h2>
<p class="section-sub t-white abs" style="top:2088px">Lorem ipsum is simply dummy text of the printing and typesetting industry.</p>

<article class="fcard abs" style="left:100px;top:2140px">
  <div class="fcard-photo" style="background:linear-gradient(135deg,#4a2a8a,#e04aa0)" role="img" aria-label="Photo of a concert stage in pink light"></div>
  <div class="fcard-lower"><div class="fcard-strip"><svg width="16" height="16" viewBox="0 0 16 16"><rect x="1" y="3" width="14" height="12" fill="none" stroke="#fff" stroke-width="1.6"/><path d="M1 7h14" stroke="#fff" stroke-width="1.6"/></svg><svg width="16" height="16" viewBox="0 0 16 16"><circle cx="8" cy="8" r="6.5" fill="none" stroke="#fff" stroke-width="1.6"/><path d="M8 4v4l3 2" stroke="#fff" stroke-width="1.6" fill="none"/></svg></div>
  <div class="fcard-body"><h4>Live Music</h4><p>Lorem ipsum is simply dummy text of the printing and typesetting industry.</p></div></div>
</article>
<article class="fcard abs" style="left:354px;top:2140px">
  <div class="fcard-photo" style="background:linear-gradient(135deg,#6a1a2a,#e05a4a)" role="img" aria-label="Photo of a party crowd in red light"></div>
  <div class="fcard-lower"><div class="fcard-strip"><svg width="16" height="16" viewBox="0 0 16 16"><rect x="1" y="3" width="14" height="12" fill="none" stroke="#fff" stroke-width="1.6"/><path d="M1 7h14" stroke="#fff" stroke-width="1.6"/></svg><svg width="16" height="16" viewBox="0 0 16 16"><circle cx="8" cy="8" r="6.5" fill="none" stroke="#fff" stroke-width="1.6"/><path d="M8 4v4l3 2" stroke="#fff" stroke-width="1.6" fill="none"/></svg></div>
  <div class="fcard-body"><h4>Nightlife</h4><p>Lorem ipsum is simply dummy text of the printing and typesetting industry.</p></div></div>
</article>
<article class="fcard abs" style="left:608px;top:2140px">
  <div class="fcard-photo" style="background:linear-gradient(180deg,#a8c8e8,#5a8a4a)" role="img" aria-label="Photo of an outdoor festival field with tents"></div>
  <div class="fcard-lower"><div class="fcard-strip"><svg width="16" height="16" viewBox="0 0 16 16"><rect x="1" y="3" width="14" height="12" fill="none" stroke="#fff" stroke-width="1.6"/><path d="M1 7h14" stroke="#fff" stroke-width="1.6"/></svg><svg width="16" height="16" viewBox="0 0 16 16"><circle cx="8" cy="8" r="6.5" fill="none" stroke="#fff" stroke-width="1.6"/><path d="M8 4v4l3 2" stroke="#fff" stroke-width="1.6" fill="none"/></svg></div>
  <div class="fcard-body"><h4>Festivals</h4><p>Lorem ipsum is simply dummy text of the printing and typesetting industry.</p></div></div>
</article>
<article class="fcard abs" style="left:862px;top:2140px">
  <div class="fcard-photo" style="background:linear-gradient(135deg,#8a3a3a,#d8b8a8)" role="img" aria-label="Photo of friends laughing at a comedy night"></div>
  <div class="fcard-lower"><div class="fcard-strip"><svg width="16" height="16" viewBox="0 0 16 16"><rect x="1" y="3" width="14" height="12" fill="none" stroke="#fff" stroke-width="1.6"/><path d="M1 7h14" stroke="#fff" stroke-width="1.6"/></svg><svg width="16" height="16" viewBox="0 0 16 16"><circle cx="8" cy="8" r="6.5" fill="none" stroke="#fff" stroke-width="1.6"/><path d="M8 4v4l3 2" stroke="#fff" stroke-width="1.6" fill="none"/></svg></div>
  <div class="fcard-body"><h4>Comedy</h4><p>Lorem ipsum is simply dummy text of the printing and typesetting industry.</p></div></div>
</article>
<a class="btn abs" style="top:2548px"><svg width="16" height="12" viewBox="0 0 16 12"><rect x="1" y="1" width="14" height="10" rx="2" fill="none" stroke="#fff" stroke-width="1.6"/><circle cx="8" cy="6" r="2" fill="#fff"/></svg>READ MORE</a>

<!-- videos -->
<h2 class="section-title t-orange abs" style="top:2680px">VIDEOS</h2>
<div class="video-main abs" role="img" aria-label="Video still of a studio microphone under stage lights"></div>
<svg class="play abs" width="76" height="56" viewBox="0 0 76 56"><rect width="76" height="56" rx="10" fill="#111" opacity=".85"/><path d="M30 16v24l20-12z" fill="#fff"/></svg>

<div class="video-item abs" style="top:2760px"><div class="video-thumb thumb-a" role="img" aria-label="Video thumbnail of an outdoor concert"></div><div><h4>LIVE MUSIC</h4><p>Lorem ipsum is simply dummy text of the printing and typesetting industry.</p></div></div>
<div class="video-item abs" style="top:2868px"><div class="video-thumb thumb-b" role="img" aria-label="Video thumbnail of a singer on stage"></div><div><h4>LIVE MUSIC</h4><p>Lorem ipsum is simply dummy text of the printing and typesetting industry.</p></div></div>
<div class="video-item abs" style="top:2976px"><div class="video-thumb thumb-c" role="img" aria-label="Video thumbnail of a band in black and white"></div><div><h4>LIVE MUSIC</h4><p>Lorem ipsum is simply dummy text of the printing and typesetting industry.</p></div></div>
<a class="btn abs" style="top:3096px"><svg width="16" height="12" viewBox="0 0 16 12"><rect x="1" y="1" width="14" height="10" rx="2" fill="none" stroke="#fff" stroke-width="1.6"/><circle cx="8" cy="6" r="2" fill="#fff"/></svg>READ MORE</a>

<!-- footer -->
<footer class="site-footer abs"></footer>
<h4 class="footer-h abs" style="left:100px;top:3200px">VENUE MAP</h4>
<div class="map abs" role="img" aria-label="Street map showing the venue location"></div>
<p class="copyright abs">copyright@2017 Bandwise</p>

<h4 class="footer-h abs" style="left:480px;top:3200px">CONTACT US</h4>
<div class="contact-line abs" style="top:3240px"><svg width="14" height="18" viewBox="0 0 14 18"><path d="M7 17S1 10 1 6.5a6 6 0 0 1 12 0C13 10 7 17 7 17z" fill="#ccc"/><circle cx="7" cy="6.5" r="2" fill="#333"/></svg><span>Lorem ipsum is simply dummy text of the printing and typesetting industry.</span></div>
<div class="contact-line abs" style="top:3300px"><svg width="14" height="16" viewBox="0 0 14 16"><path d="M3 1l3 4-2 2c1 2 3 4 5 5l2-2 3 3-2 2C6 15-1 8 1 3z" fill="#ccc"/></svg><span>020 7946 0183</span></div>
<div class="contact-line abs" style="top:3340px"><svg width="16" height="12" viewBox="0 0 16 12"><rect x=".8" y=".8" width="14.4" height="10.4" fill="none" stroke="#ccc" stroke-width="1.5"/><path d="M1 1l7 6 7-6" stroke="#ccc" stroke-width="1.5" fill="none"/></svg><span>rvkm47@postlane.net</span></div>
<div class="footer-social abs"><span>Chatterbox</span><span>Flitter</span><span>PingTalk</span><span>SMS</span></div>

<form class="register abs">
  <h4>REGISTER NOW</h4>
  <span class="field">Name</span>
  <span class="field">Email</span>
  <span class="field">Phone</span>
  <span class="field">Event</span>
  <div class="submit">SUBMIT</div>
</form>

</body>
</html>
```